Torvel’s letterhead for local government

I require a letterhead for quarterly communications with constituents. The colours I have used in the past are navy & green (together) so I’m happy to use similar colours for this. Please refer to business card as an example.
The letter must make reference to the position I hold which is as per below
“Clr Torvel Quennisbury OAM”
And the tag line I have used in the past is “Torvel on the Terrace”. Although I’m not sure if this would be used in a letterhead or not. Happy for this to be provided as an option.
I would like a photo in the letterhead as I believe face recognition is key as an elected member.

Target Market(s)

Political interests

Industry/Entity Type

Government Office

Font styles to use
Sans Serif

Requirements
Must have
• Politically professional. I have been an elected member for 2 years so it is expected that the letterhead conveys that. The colours of the business card is to be used.
Nice to have
• Background of photos to be manipulated or changed to make me stand out, if possible?
Should not have
• Looked like it’s cropped or undertaken by an amateur designer.

```html
<!DOCTYPE html>
<html lang="en">
<head>
<meta charset="utf-8">
<title>Torvel Quennisbury – Letterhead</title>
<link rel="stylesheet" href="https://fonts.googleapis.com/css2?family=Arimo:wght@400;700&family=Open+Sans:wght@400;600&display=swap">
<style>
  :root {
    --navy: #2a5d93;
    --navy-text: #1f4f8a;
    --green: #45b36b;
    --green-text: #1fa84f;
    --body-text: #4a4a4a;
    --paper: #ffffff;
  }
  * { box-sizing: border-box; margin: 0; padding: 0; }
  html, body { width: 1040px; height: 1200px; overflow: hidden; background: var(--paper); }
  .letterhead {
    position: relative; width: 1040px; height: 1200px; background: var(--paper);
    font-family: "Open Sans", sans-serif; color: var(--body-text);
  }
  .band { position: absolute; left: 0; width: 1040px; display: block; }
  .band--top { top: 0; height: 23px; }
  .band--bottom { bottom: 0; height: 32px; }

  .portrait {
    position: absolute; left: 177px; top: 37px; width: 213px; height: 191px;
    border-radius: 6px;
    background: radial-gradient(ellipse at 50% 40%, #e6e6e6 0%, #d4d4d4 55%, #c4c6ca 100%);
  }
  .identity { position: absolute; left: 424px; top: 100px; font-family: "Arimo", sans-serif; }
  .identity__name { font-size: 27px; font-weight: 700; color: var(--navy-text); letter-spacing: 0.2px; }
  .identity__role { margin-top: 14px; font-size: 20px; line-height: 26px; color: var(--green-text); }

  .letter { position: absolute; left: 99px; width: 839px; font-size: 15px; }
  .letter__date { top: 254px; }
  .letter__recipient { top: 289px; line-height: 18px; }
  .letter__salutation { top: 394px; }
  .letter__body { top: 446px; }
  .letter__body p { line-height: 27px; text-align: justify; hyphens: auto; margin-bottom: 27px; }
  .letter__closing { top: 852px; }
  .signatory { position: absolute; left: 99px; top: 930px; }
  .signatory__name { font-size: 18px; font-weight: 600; color: #3a3a3a; }
  .signatory__title { font-size: 15px; margin-top: 4px; }

  .contact {
    position: absolute; left: 0; width: 1040px; top: 1134px;
    display: flex; justify-content: center; align-items: center; gap: 8px;
    font-family: "Arimo", sans-serif; font-size: 17px; color: #222;
  }
  .contact__item { display: flex; align-items: center; gap: 4px; }
  .contact__icon { width: 20px; height: 20px; }
</style>
</head>
<body>
<main class="letterhead">
  <svg class="band band--top" viewBox="0 0 1040 23" preserveAspectRatio="none" aria-hidden="true">
    <polygon points="0,0 540,0 548,23 0,23" fill="var(--navy)"/>
    <polygon points="550,0 1040,0 1040,23 558,23" fill="var(--green)"/>
  </svg>

  <div class="portrait" role="img" aria-label="Portrait photograph of the councillor in a dark suit and tie"></div>

  <header class="identity">
    <h1 class="identity__name">Clr Torvel Quennisbury OAM</h1>
    <p class="identity__role">Candidate for Area Councillor<br>City of Marrowvale</p>
  </header>

  <p class="letter letter__date">Issuing Date: May 5, 2018</p>
  <p class="letter letter__recipient">Name Of Employee Mr. XYZABC<br>Address of Employee<br>Address Line 2 etc..</p>
  <p class="letter letter__salutation">Dear Mr.XYZABC</p>

  <section class="letter letter__body">
    <p>Lorem Ipsum has been the industry's standard dummy text ever since the 1500s, when an unknown printer took a galley of type and scrambled it to make a type specimen book. It has survived not only five centuries, but also the leap into electronic typesetting, remaining essentially unchanged. It was popularised in the 1960s with the release of Typeline sheets containing Lorem Ipsum passages, and more recently with desktop publishing software like Pagecraft Studio including versions of Lorem Ipsum.</p>
    <p>Lorem Ipsum is simply dummy text of the printing and typesetting industry. Lorem Ipsum has been the industry's standard dummy text ever since the 1500s, when an unknown printer took a galley of type and scrambled it to make a type specimen book.</p>
    <p>It has survived not only five centuries, but also the leap into electronic typesetting, remaining essentially unchanged. It was popularised in the 1960s with the release of Typeline sheets containing Lorem IpsumIpsum passages.</p>
  </section>

  <p class="letter letter__closing">Yours Sincerely</p>

  <div class="signatory">
    <p class="signatory__name">Merrick Haldane</p>
    <p class="signatory__title">Managing Director</p>
  </div>

  <footer class="contact">
    <span class="contact__item">
      <svg class="contact__icon" viewBox="0 0 20 20" aria-hidden="true">
        <circle cx="10" cy="10" r="8.5" fill="none" stroke="var(--navy)" stroke-width="1.5"/>
        <path d="M7 5.5l1.6 2.4-1 1.1c.6 1.3 1.5 2.2 2.6 2.8l1.1-1 2.4 1.5-.8 1.7c-3.4-.3-6.5-3.4-6.8-6.8z" fill="var(--navy)"/>
      </svg>044-870 215 364
    </span>
    <span class="contact__item">
      <svg class="contact__icon" viewBox="0 0 20 20" aria-hidden="true">
        <circle cx="10" cy="10" r="8.5" fill="none" stroke="var(--navy)" stroke-width="1.5"/>
        <rect x="5.5" y="7" width="9" height="6.5" rx="0.8" fill="var(--navy)"/>
        <path d="M5.8 7.3L10 10.6l4.2-3.3" fill="none" stroke="#fff" stroke-width="1"/>
      </svg>hello@torvelcouncil.org
    </span>
    <span class="contact__item">
      <svg class="contact__icon" viewBox="0 0 20 20" aria-hidden="true">
        <circle cx="10" cy="10" r="8.5" fill="none" stroke="var(--navy)" stroke-width="1.5"/>
        <circle cx="10" cy="10" r="5" fill="var(--navy)"/>
        <path d="M5 10h10M10 5v10M10 5c-2 2.5-2 7.5 0 10M10 5c2 2.5 2 7.5 0 10" fill="none" stroke="#fff" stroke-width="0.8"/>
      </svg>www.torvelcouncil.org
    </span>
  </footer>

  <svg class="band band--bottom" viewBox="0 0 1040 32" preserveAspectRatio="none" aria-hidden="true">
    <polygon points="0,0 526,0 534,32 0,32" fill="var(--navy)"/>
    <polygon points="535,0 1040,0 1040,32 543,32" fill="var(--green)"/>
  </svg>
</main>
</body>
</html>
```